Business Card Design Project

We are an incubator company that helps young entrepreneur to launch new ideas into the market. We will be targeting investors or likewise; Angels, young entrepreneurs and technopreneurs.

Our logo is being tasked by pixelhive to design, therefore there is no logo for now.
You can us Lanternfield Pte Ltd as the logo for the time being.

Please let us have some versions of modern and yet professional designs; for words, you can indicate e.g (address), (Title)

thanks

Target Market(s)

young entrepreneurs
angels, investors

Industry/Entity Type

Business

Colors
3176b5
ffffff

Requirements
Must have
• able to project out our name; Lanternfield
Should not have
• Nothing childish or cartoon

```html
<!DOCTYPE html>
<html lang="en">
<head>
<meta charset="utf-8">
<title>Lanternfield Business Card</title>
<link rel="stylesheet" href="https://fonts.googleapis.com/css2?family=Arimo:wght@400;700&family=Mukta:wght@600;700&display=swap">
<style>
  :root {
    --brand-blue: #3176b5;
    --card-white: #ffffff;
    --stage-grey: #d6d6d6;
    --ink: #1a1a1a;
    --muted: #6a7480;
    --ghost-blue: rgba(49, 118, 181, 0.09);
  }
  * { box-sizing: border-box; margin: 0; padding: 0; }
  html, body {
    width: 1200px;
    height: 900px;
    overflow: hidden;
    background: var(--stage-grey);
  }
  .stage {
    position: relative;
    width: 1200px;
    height: 900px;
    display: flex;
    align-items: center;
    justify-content: center;
    gap: 40px;
  }
  .card {
    position: relative;
    width: 540px;
    height: 310px;
    background: var(--card-white);
    border-radius: 26px;
    overflow: hidden;
    box-shadow: 0 10px 24px rgba(0, 0, 0, 0.12);
  }

  /* Front */
  .card-front__wave {
    position: absolute;
    left: 0;
    top: 20px;
    width: 540px;
    height: 260px;
    background:
      radial-gradient(ellipse 60% 40% at 18% 30%, rgba(150, 158, 180, 0.35), transparent 70%),
      radial-gradient(ellipse 55% 30% at 70% 80%, rgba(150, 158, 180, 0.30), transparent 70%),
      linear-gradient(160deg, rgba(201, 204, 214, 0.25), transparent 60%);
  }
  .brand {
    position: absolute;
    left: 80px;
    top: 70px;
    width: 300px;
    display: flex;
    flex-direction: column;
    align-items: center;
  }
  .brand__square {
    width: 72px;
    height: 72px;
    background: var(--brand-blue);
    margin-bottom: 22px;
  }
  .brand__name {
    font-family: "Mukta", sans-serif;
    font-weight: 700;
    font-size: 46px;
    line-height: 1;
    letter-spacing: 1px;
    text-transform: uppercase;
    color: var(--brand-blue);
    white-space: nowrap;
  }
  .brand__tagline {
    margin-top: 6px;
    font-family: "Mukta", sans-serif;
    font-weight: 600;
    font-size: 11px;
    letter-spacing: 3.2px;
    text-transform: uppercase;
    color: var(--muted);
    white-space: nowrap;
  }

  /* Back */
  .card-back__ghost {
    position: absolute;
    left: 40px;
    top: 30px;
    width: 250px;
    height: 250px;
    background: var(--ghost-blue);
  }
  .contact {
    position: absolute;
    top: 108px;
    left: 118px;
    display: flex;
    align-items: stretch;
    font-family: "Arimo", sans-serif;
  }
  .contact__person {
    text-align: right;
    padding-right: 14px;
    padding-top: 4px;
  }
  .contact__name {
    font-size: 19px;
    font-weight: 700;
    color: var(--brand-blue);
    white-space: nowrap;
  }
  .contact__title {
    margin-top: 4px;
    font-size: 13px;
    color: var(--ink);
  }
  .contact__divider {
    width: 2px;
    background: var(--ink);
  }
  .contact__list {
    list-style: none;
    padding-left: 14px;
  }
  .contact__item {
    display: flex;
    align-items: center;
    gap: 6px;
    font-size: 15px;
    line-height: 21px;
    color: var(--ink);
    white-space: nowrap;
  }
  .contact__icon {
    width: 17px;
    height: 17px;
    flex: none;
    fill: var(--brand-blue);
  }
</style>
</head>
<body>
<main class="stage">
  <section class="card card-front" aria-label="Card front">
    <div class="card-front__wave" role="img" aria-label="Flowing fine-line wave pattern in soft grey"></div>
    <div class="brand">
      <div class="brand__square"></div>
      <p class="brand__name">Lanternfield</p>
      <p class="brand__tagline">Launching Ideas Into Markets</p>
    </div>
  </section>

  <section class="card card-back" aria-label="Card back">
    <div class="card-back__ghost"></div>
    <div class="contact">
      <div class="contact__person">
        <p class="contact__name">Dana Whitfield</p>
        <p class="contact__title">Manager</p>
      </div>
      <div class="contact__divider"></div>
      <ul class="contact__list">
        <li class="contact__item">
          <svg class="contact__icon" viewBox="0 0 24 24" aria-hidden="true"><path d="M6.6 10.8a15.1 15.1 0 0 0 6.6 6.6l2.2-2.2c.3-.3.7-.4 1-.2 1.1.4 2.3.6 3.6.6.6 0 1 .4 1 1V20c0 .6-.4 1-1 1A17 17 0 0 1 3 4c0-.6.4-1 1-1h3.5c.6 0 1 .4 1 1 0 1.2.2 2.4.6 3.6.1.3 0 .7-.2 1z"/></svg>
          919 555 0142
        </li>
        <li class="contact__item">
          <svg class="contact__icon" viewBox="0 0 24 24" aria-hidden="true"><path d="M12 2a10 10 0 1 0 0 20 10 10 0 0 0 0-20zm6.9 6h-3a15.6 15.6 0 0 0-1.3-3.6A8 8 0 0 1 18.9 8zM12 4c.8 1.2 1.5 2.5 1.9 4h-3.8c.4-1.5 1.1-2.8 1.9-4zM4.3 14a8.2 8.2 0 0 1 0-4h3.4a16.5 16.5 0 0 0 0 4zm.8 2h3a15.6 15.6 0 0 0 1.3 3.6A8 8 0 0 1 5.1 16zm3-8h-3a8 8 0 0 1 4.3-3.6C8.8 5.5 8.4 6.7 8.1 8zM12 20c-.8-1.2-1.5-2.5-1.9-4h3.8c-.4 1.5-1.1 2.8-1.9 4zm2.3-6H9.7a14.7 14.7 0 0 1 0-4h4.6a14.7 14.7 0 0 1 0 4zm.3 5.6c.6-1.1 1-2.3 1.3-3.6h3a8 8 0 0 1-4.3 3.6zm1.7-5.6a16.5 16.5 0 0 0 0-4h3.4a8.2 8.2 0 0 1 0 4z"/></svg>
          www.lanternfield.com
        </li>
        <li class="contact__item">
          <svg class="contact__icon" viewBox="0 0 24 24" aria-hidden="true"><path d="M3 5h18c.6 0 1 .4 1 1v12c0 .6-.4 1-1 1H3c-.6 0-1-.4-1-1V6c0-.6.4-1 1-1zm1 2.2V17h16V7.2l-8 5.3z"/></svg>
          hello@lanternfield.com
        </li>
        <li class="contact__item">
          <svg class="contact__icon" viewBox="0 0 24 24" aria-hidden="true"><path d="M12 3 2 12h3v8h5v-5h4v5h5v-8h3z"/></svg>
          Millbrook, North Carolina
        </li>
      </ul>
    </div>
  </section>
</main>
</body>
</html>
```